QP Fiduciary Website Redesign Contest

We want to refresh our website to be more insitutional, professional for an international audience. We have designed a new logo for this purpose and that has been attached. A full brand brief and positioning statement has also been attached. Please read through all the documents carefully before designing. The old website is found here: https://qp-fiduciary.example/

Target Market(s)

Actuaries and associated businesses internationally

Industry/Entity Type

professional services - actuaries

Number of Pages Required

3 page

Font styles to use
Sans Serif

Colors
0054AA
0677BA
7BADD7
CADEEF
E8F1F8
0094D4
00A9DD
6FCCEA
C7EBF8
E9F6FB
F0912C
F2A743
F7CA91
FBE8D2
FDF5EE
EE7325
F08F49
F5BC92
FAE3D3
FDF4ED
EB3D1F
EC4F4E
F09395
F8D3D4
FCEDEE

Requirements
Must have
• blues and greens to match the logo color, complimentary colors, navigation
Nice to have
• old site: https://qp-fiduciary.example/

```html
<!DOCTYPE html>
<html lang="en">
<head>
<meta charset="utf-8">
<title>QP Fiduciary — Actuarial Software</title>
<link href="https://fonts.googleapis.com/css2?family=Inter:wght@400;500;600;700;800&display=swap" rel="stylesheet">
<style>
:root{
  --backdrop:#adabae;
  --blue-deep:#0054aa;
  --blue:#0677ba;
  --blue-bright:#0094d4;
  --cyan:#00a9dd;
  --cyan-soft:#6fccea;
  --blue-pale:#e8f1f8;
  --orange:#ee7325;
  --amber:#f0912c;
  --red:#eb3d1f;
  --navy:#0a1e38;
  --ink:#111;
  --muted:#555;
  --soft:#f4f7fa;
  --white:#fff;
  --line:#e3e3e3;
}
*{box-sizing:border-box;margin:0;padding:0}
html,body{width:1200px;height:2301px;overflow:hidden}
body{background:var(--backdrop);font-family:"Inter",Arial,sans-serif;color:var(--ink)}
.page{position:absolute;left:95px;top:95px;width:1011px;height:2110px;background:var(--white);box-shadow:0 10px 30px rgba(0,0,0,.25);overflow:hidden}

/* header */
.site-header{height:63px;display:flex;align-items:center;justify-content:space-between;padding:0 17px 0 12px;background:var(--white)}
.brand{display:flex;align-items:center;gap:8px;font-size:21px;font-weight:600;letter-spacing:.5px;color:var(--ink)}
.brand-dot{width:12px;height:12px;border-radius:50%;background:var(--blue-bright)}
.main-nav{display:flex;align-items:center;gap:18px;font-size:11.5px}
.main-nav a{color:var(--ink);text-decoration:none}
.main-nav .nav-cta{background:var(--blue-deep);color:var(--white);font-weight:700;padding:8px 12px;border-radius:16px}

/* hero */
.hero{position:relative;height:366px;background:linear-gradient(110deg,var(--blue-deep) 0%,var(--blue) 45%,var(--blue-bright) 75%,var(--cyan) 100%);color:var(--white);text-align:center;overflow:hidden}
.hero-content{position:relative;padding-top:93px}
.hero h1{font-size:37px;font-weight:800;line-height:40px;letter-spacing:-.2px}
.hero p{margin-top:13px;font-size:15px;line-height:25px}
.btn-amber{display:inline-block;margin-top:10px;background:var(--amber);color:var(--white);font-weight:700;font-size:13.5px;padding:9px 17px;border-radius:18px;text-decoration:none}

/* overview */
.overview{height:339px;background:var(--navy);color:var(--white);text-align:center;padding-top:80px}
.section-title{font-size:36px;font-weight:800;letter-spacing:-.2px;text-transform:uppercase;line-height:40px}
.overview p{width:700px;margin:28px auto 0;font-size:15px;line-height:20px}
.btn-outline{display:inline-block;margin-top:15px;border:1.5px solid var(--white);color:var(--white);font-weight:700;font-size:14px;padding:6px 14px;border-radius:16px;text-decoration:none}

/* solutions */
.solutions{height:477px;background:var(--soft);padding-top:81px;text-align:center}
.card-row{display:flex;gap:26px;justify-content:center;margin-top:53px}
.card{width:262px;height:223px;background:var(--white);border-radius:6px;box-shadow:0 2px 10px rgba(0,0,0,.06);padding-top:29px}
.icon-ring{width:56px;height:56px;border-radius:50%;border:1.5px solid var(--blue-bright);background:var(--white);display:flex;align-items:center;justify-content:center;margin:0 auto}
.card h3{margin-top:15px;font-size:15.5px;font-weight:700}
.card p{margin:8px auto 0;width:230px;font-size:11.5px;line-height:16.5px;color:var(--muted)}
.learn-more{display:inline-block;margin-top:7px;font-size:11.5px;font-weight:700;color:var(--orange);text-decoration:none}

/* characteristics */
.characteristics{height:391px;background:var(--white);padding-top:70px;text-align:center}
.feature-grid{position:relative;width:837px;margin:48px auto 0;display:grid;grid-template-columns:419px 418px;text-align:left}
.feature-grid::before{content:"";position:absolute;left:419px;top:0;bottom:0;width:1px;background:var(--line)}
.feature-grid::after{content:"";position:absolute;left:0;right:0;top:91px;height:1px;background:var(--line)}
.feature{display:flex;align-items:center;gap:11px;height:91px;padding-bottom:6px}
.feature:nth-child(3),.feature:nth-child(4){height:101px;padding-top:10px}
.feature:nth-child(even){padding-left:41px}
.feature .icon-ring{width:62px;height:62px;margin:0;flex:none}
.feature h4{font-size:15.5px;font-weight:700}
.feature p{margin-top:3px;font-size:10.5px;line-height:16px;color:var(--muted);white-space:nowrap}

/* cta */
.cta{height:285px;background:var(--orange);text-align:center;padding-top:82px}
.cta .section-title{color:var(--navy)}
.btn-navy{display:inline-block;margin-top:40px;background:var(--navy);color:var(--white);font-weight:700;font-size:19px;padding:13px 26px;border-radius:24px;text-decoration:none}

/* footer */
.site-footer{height:189px;background:var(--navy);color:var(--white);padding:32px 0 0 158px;position:relative}
.footer-cols{display:flex}
.footer-col{width:179px}
.footer-col h5{font-size:10px;font-weight:700;margin-bottom:10px}
.footer-col a{display:block;font-size:9px;color:var(--white);text-decoration:none;line-height:18px}
.copyright{position:absolute;left:0;right:0;top:147px;text-align:center;font-size:7.5px;color:#c7d3e0}
</style>
</head>
<body>
<div class="page">

  <header class="site-header">
    <div class="brand"><span class="brand-dot"></span>QP Fiduciary</div>
    <nav class="main-nav">
      <a href="#">Home</a><a href="#">Platform</a><a href="#">Solutions</a><a href="#">Insights</a><a href="#">Company</a><a href="#">Contact</a>
      <a href="#" class="nav-cta">Request a Technical Walkthrough</a>
    </nav>
  </header>

  <section class="hero">
    <div class="hero-content">
      <h1>Actuarial software for structured,<br>auditable financial analysis</h1>
      <p>Software that translates actuarial methodologies into disciplined<br>decision-ready analytical tools across diverse regulatory environments.</p>
      <a href="#" class="btn-amber">Request a Technical Walkthrough</a>
    </div>
  </section>

  <section class="overview">
    <h2 class="section-title">Platform Overview</h2>
    <p>QP Fiduciary develops modular actuarial software designed to support reserving, valuation, pricing and enterprise risk management workflows across diverse regulatory environments. Our platform translates established actuarial methodologies into disciplined, audit-ready tools, ensuring transparency and governance at every step.</p>
    <a href="#" class="btn-outline">EXPLORE PLATFORM</a>
  </section>

  <section class="solutions">
    <h2 class="section-title">Core Solutions</h2>
    <div class="card-row">
      <article class="card">
        <div class="icon-ring"><svg width="30" height="30" viewBox="0 0 30 30" fill="none" stroke="#0054aa" stroke-width="1.3"><rect x="3" y="4" width="24" height="16" rx="1"/><line x1="15" y1="20" x2="15" y2="25"/><line x1="9" y1="26" x2="21" y2="26"/><line x1="7" y1="9" x2="13" y2="9"/><line x1="7" y1="13" x2="13" y2="13"/><rect x="16" y="8" width="8" height="8"/></svg></div>
        <h3>Reserving &amp; Valuation</h3>
        <p>Structured workflows and financial reporting across jurisdictions built on disciplined actuarial methodologies.</p>
        <a href="#" class="learn-more">Learn more →</a>
      </article>
      <article class="card">
        <div class="icon-ring"><svg width="30" height="30" viewBox="0 0 30 30" fill="none" stroke="#0054aa" stroke-width="1.3"><rect x="3" y="4" width="20" height="15" rx="1"/><polyline points="6,15 10,10 14,13 19,7"/><circle cx="19" cy="20" r="5"/><line x1="23" y1="24" x2="27" y2="28"/></svg></div>
        <h3>Pricing</h3>
        <p>Insurance and reinsurance pricing models grounded in transparency, enabling accurate, explainable decisions.</p>
        <a href="#" class="learn-more">Learn more →</a>
      </article>
      <article class="card">
        <div class="icon-ring"><svg width="30" height="30" viewBox="0 0 30 30" fill="none" stroke="#0054aa" stroke-width="1.3"><rect x="4" y="10" width="10" height="16"/><rect x="14" y="6" width="7" height="20"/><line x1="7" y1="14" x2="11" y2="14"/><line x1="7" y1="18" x2="11" y2="18"/><circle cx="23" cy="21" r="4"/><polygon points="22,4 26,12 18,12"/></svg></div>
        <h3>Enterprise Risk Management</h3>
        <p>Tools supporting reinsurance optimization and capital modeling for comprehensive enterprise risk management.</p>
        <a href="#" class="learn-more">Learn more →</a>
      </article>
    </div>
  </section>

  <section class="characteristics">
    <h2 class="section-title">Platform Characteristics</h2>
    <div class="feature-grid">
      <div class="feature">
        <div class="icon-ring"><svg width="32" height="32" viewBox="0 0 32 32" fill="none" stroke="#0054aa" stroke-width="1.3"><rect x="4" y="5" width="6" height="5"/><circle cx="16" cy="7.5" r="2.5"/><rect x="22" y="5" width="6" height="5"/><rect x="4" y="14" width="6" height="5"/><circle cx="22" cy="16.5" r="2.5"/><rect x="4" y="23" width="6" height="5"/><polygon points="22,22 25,25.5 22,29 19,25.5"/><line x1="10" y1="7.5" x2="13.5" y2="7.5"/><line x1="10" y1="16.5" x2="19.5" y2="16.5"/><line x1="10" y1="25.5" x2="19" y2="25.5"/></svg></div>
        <div><h4>Structured Workflows</h4><p>Disciplined processes built to support multi-jurisdictional<br>review and actuarial governance.</p></div>
      </div>
      <div class="feature">
        <div class="icon-ring"><svg width="32" height="32" viewBox="0 0 32 32" fill="none" stroke="#0054aa" stroke-width="1.3"><circle cx="16" cy="13" r="9"/><circle cx="16" cy="13" r="3"/><line x1="10" y1="21" x2="10" y2="28"/><line x1="22" y1="21" x2="22" y2="28"/></svg></div>
        <div><h4>Transparent Assumptions</h4><p>Clear documentation of assumptions and methodologies<br>for auditability and defensibility.</p></div>
      </div>
      <div class="feature">
        <div class="icon-ring"><svg width="32" height="32" viewBox="0 0 32 32" fill="none" stroke="#0054aa" stroke-width="1.3"><rect x="6" y="4" width="16" height="22" rx="1"/><rect x="11" y="8" width="16" height="21" rx="1" fill="#fff"/><line x1="14" y1="13" x2="24" y2="13"/><line x1="14" y1="17" x2="24" y2="17"/><line x1="14" y1="21" x2="24" y2="21"/><line x1="14" y1="25" x2="20" y2="25"/></svg></div>
        <div><h4>Comparative Analysis</h4><p>Capabilities for scenario comparison and sensitivity<br>analysis to inform professional judgment.</p></div>
      </div>
      <div class="feature">
        <div class="icon-ring"><svg width="32" height="32" viewBox="0 0 32 32" fill="none" stroke="#0054aa" stroke-width="1.3"><circle cx="16" cy="12" r="6"/><circle cx="16" cy="12" r="2"/><path d="M4 18 L10 24 L16 26 L22 24 L28 18"/><path d="M7 28 L12 24 M25 28 L20 24"/></svg></div>
        <div><h4>Governance Ready</h4><p>Outputs designed to support regulator and board review,<br>ensuring compliance and clarity.</p></div>
      </div>
    </div>
  </section>

  <section class="cta">
    <h2 class="section-title">Interested in Exploring the Platform?</h2>
    <a href="#" class="btn-navy">Request a Technical Walkthrough</a>
  </section>

  <footer class="site-footer">
    <div class="footer-cols">
      <div class="footer-col"><h5>Company</h5><a href="#">About</a><a href="#">Careers</a><a href="#">Legal</a></div>
      <div class="footer-col"><h5>Platform</h5><a href="#">Overview</a><a href="#">Reserving &amp; Valuation</a><a href="#">Pricing</a><a href="#">Enterprise Risk Management</a></div>
      <div class="footer-col"><h5>Insights</h5><a href="#">Articles</a><a href="#">Guides</a><a href="#">News</a></div>
      <div class="footer-col"><h5>Contact</h5><a href="#">Email Us</a><a href="#">Request a Walkthrough</a></div>
    </div>
    <p class="copyright">© 2026 QP Fiduciary. All rights reserved.</p>
  </footer>

</div>
</body>
</html>
```